The Harrowgate

We need a APP for our members. this is a Private Bar/Venue. history of the brick building is it was built in1898 and was a gentleman club, oyster house, cigar factory and then law offices before we purchased and are beginning restoration.
the APP must include
1. direct texting to the concierge
2. calendar of events
3. Pellmont Lock To open the lock, anyone with a code can approach the door, enable their phone's Bluetooth and press the relevant address from the app.
Read more: http://www.brevinpost.example/tech/article-5521840/keyless-entry-phone-door-lock-explained.html#qq7rTb2mWx
4. Menus from various restaurants from our surrounding area
5. member name and member number to give the feel that the app is personalized
6. the members account balance
7. ability to pay their bill with credit card or pim coin monthly and automatically.
8. link to zirva with its own icon within the app.
9.the ability to reserve the room
Anything else that may of interest for our members that may be relevant that I may not have mentioned since we are new at this...
35 to 60 years of age
Club
Designer to choose colors to be used in the design.

```html
<!DOCTYPE html>
<html lang="en">
<head>
<meta charset="utf-8">
<title>The Harrowgate – Sign in</title>
<link href="https://fonts.googleapis.com/css2?family=Open+Sans:wght@400&display=swap" rel="stylesheet">
<style>
  :root {
    --paper: #ffffff;
    --ink: #111111;
    --tab-active: #4b4b4b;
    --tab-idle: #9b9b9b;
    --tab-text: #ffffff;
    --label: #a2a2a2;
    --rule: #8f8f8f;
  }
  * { margin: 0; padding: 0; box-sizing: border-box; }
  html, body {
    width: 675px;
    height: 1200px;
    overflow: hidden;
    background: var(--paper);
  }
  .screen {
    position: relative;
    width: 675px;
    height: 1200px;
    background: var(--paper);
    font-family: "Open Sans", "Segoe UI", sans-serif;
  }
  .brand {
    position: absolute;
    top: 150px;
    left: 0;
    width: 100%;
    display: flex;
    flex-direction: column;
    align-items: center;
  }
  .brand-square {
    width: 66px;
    height: 66px;
    background: var(--ink);
  }
  .brand-name {
    margin-top: 58px;
    font-size: 36px;
    font-weight: 400;
    letter-spacing: 5px;
    color: var(--ink);
    text-transform: uppercase;
  }
  .auth-tabs {
    position: absolute;
    top: 495px;
    left: 0;
    width: 100%;
    height: 83px;
    display: flex;
  }
  .auth-tab {
    flex: 1;
    display: flex;
    align-items: center;
    justify-content: center;
    color: var(--tab-text);
    font-size: 33px;
  }
  .auth-tab--active { background: var(--tab-active); }
  .auth-tab--idle { background: var(--tab-idle); }
  .field {
    position: absolute;
    left: 70px;
    width: 535px;
    border-bottom: 2px solid var(--rule);
  }
  .field--username { top: 638px; height: 67px; }
  .field--password { top: 784px; height: 70px; }
  .field-label {
    font-size: 24px;
    color: var(--label);
  }
  .forgot-link {
    position: absolute;
    right: 0;
    top: 9px;
    font-size: 15px;
    color: var(--label);
  }
</style>
</head>
<body>
  <main class="screen">
    <header class="brand">
      <div class="brand-square"></div>
      <h1 class="brand-name">The Harrowgate</h1>
    </header>

    <nav class="auth-tabs">
      <div class="auth-tab auth-tab--active">Sign in</div>
      <div class="auth-tab auth-tab--idle">Sign up</div>
    </nav>

    <div class="field field--username">
      <span class="field-label">Username:</span>
    </div>

    <div class="field field--password">
      <span class="field-label">Password:</span>
      <span class="forgot-link">Forgot password?</span>
    </div>
  </main>
</body>
</html>
```